Commercial/Corporate Law Firm needs Website Design

Hi guys. I've started up a new law firm and would love your help designing an attractive website. I'll need both design and coding, and to make it easy for us to edit as necessary later, I think it should be built off a Wordpress.org structure.
FIRST IMPRESSIONS
It's very important that the first impression of the website really captures our prospective clients' attention and impresses them. Their first three seconds needs to be good.
I imagine the homepage may be short, with a menu bar and a compelling image, and with a tagline overlaid or underneath (eg. "It's about results.")
The image should be related to our practice areas: eg. IPOs, corporate transactions, or commercial negotiations.
I have previously suggested there could be a skyline image of Sydney or Adelaide. However, because we are based in Adelaide, I don't think Sydney is appropriate - and Adelaide is probably too boring to use.
HOMEPAGE
Being a new firm, we don't have many existing testimonials, and I will be the only lawyer to start with. So we need to focus on the nature of the services we will provide and how my experience can help them. We have an existing logo to use, and I would like the website colour scheme not to clash with that logo (dark blue and white).
After the initial image and tagline there should be a brief introduction to each of the main areas of work, eg. "We specialise in three main areas of practice:"
1. Corporate Transactions and Regulation
2. Business Law and Dispute Resolution
3. Migration Assistance
These should each have an appropriate photo and link to a separate page that briefly describes our services in that area.
Below that there should be a message from me with a photo. Finally, at the bottom, there should be a "Contact Us" section which shows a Google image of our address, contact details, and then our logo with colours inverted.
OTHER PAGES
While we will need some other pages, they should all be fairly simple. I think we will need one page to say "About Us", where I will put information about my experience. I think we will then need one page for each of the 3 areas listed above, which just needs an appropriate image and then text to describe the service. Finally, a "Contact Us" page which I imagine will be the same as the bottom of the homepage.
OTHER DETAILS
For now you can use details from my LinkedIn page to fill out any other text as necessary, or the photo.
Because the logo is square, I would prefer the design of the website also to be rectangular.
Looking forward to seeing your work! Thank you.
Marcus
Potential clients:
Businesses with legal issues or disputes
Companies wishing to list on the stock market

```html
<!DOCTYPE html>
<html lang="en">
<head>
<meta charset="utf-8">
<title>Corvell Legal</title>
<link rel="stylesheet" href="https://fonts.googleapis.com/css2?family=Libre+Baskerville:wght@400;700&family=Montserrat:wght@600;700&family=Work+Sans:wght@400;500;600&display=swap">
<style>
:root{
  --navy:#1c3461;
  --ink:#1f1f1f;
  --text:#6f6f6f;
  --muted:#9a9a9a;
  --line:#e3e3e3;
  --panel:#f3f3f3;
  --white:#ffffff;
  --footer:#2c2c2c;
  --black:#111111;
  --pin:#e0504a;
}
*{box-sizing:border-box;margin:0;padding:0}
html,body{width:1200px;height:3586px;overflow:hidden}
body{background:var(--white);font-family:"Work Sans",sans-serif;color:var(--text);position:relative}

/* header */
.site-header{position:absolute;top:0;left:0;width:1200px;height:144px;background:var(--white)}
.brand{position:absolute;left:128px;top:20px;width:130px;text-align:center}
.brand-square{width:50px;height:50px;background:var(--navy);margin:0 auto 10px}
.brand-name{font-family:"Work Sans",sans-serif;font-weight:600;font-size:19px;letter-spacing:3px;line-height:1.25;color:var(--navy);white-space:nowrap}
.topbar{position:absolute;right:86px;top:28px;font-size:15px;font-weight:500;color:var(--navy);display:flex;align-items:center;gap:8px}
.topbar svg{width:14px;height:14px;fill:var(--navy)}
.topbar .sep{margin:0 8px}
.main-nav{position:absolute;right:86px;top:76px;display:flex;align-items:center;gap:38px;font-size:14px;font-weight:500;color:var(--ink)}
.quote-btn{background:var(--navy);color:var(--white);padding:11px 13px;font-size:14px}

/* hero */
.hero{position:absolute;top:144px;left:0;width:1200px;height:478px;
  background:linear-gradient(180deg,#7d86b4 0%,#9a9cc4 22%,#c7b6c0 36%,#d8c2b4 42%,#8a8796 46%,#5f6476 56%,#6c6a72 66%,#3f4e6e 74%,#5676ac 82%,#7f9dcd 92%,#5a79b0 100%)}
.hero-box{position:absolute;left:347px;top:131px;width:506px;height:215px;background:rgba(255,255,255,.82);text-align:center}
.hero-title{font-family:"Montserrat",sans-serif;font-weight:700;font-size:46px;color:var(--navy);letter-spacing:1px;margin-top:48px}
.btn-dark{display:inline-block;background:var(--black);color:var(--white);font-family:"Montserrat",sans-serif;font-weight:600;font-size:12px;letter-spacing:.5px;padding:11px 24px}
.hero-box .btn-dark{margin-top:20px}

/* section heads */
.section-title{position:absolute;left:0;width:1200px;text-align:center;font-family:"Libre Baskerville",serif;font-weight:400;font-size:36px;color:var(--navy)}
.section-rule{position:absolute;left:564px;width:72px;height:2px;background:var(--navy)}
.section-sub{position:absolute;left:0;width:1200px;text-align:center;font-size:18px;color:var(--navy)}

/* practice grid */
.practice-grid{position:absolute;left:100px;top:870px;width:1000px;height:670px;display:grid;grid-template-columns:333px 334px 333px;grid-template-rows:335px 335px;box-shadow:0 2px 12px rgba(0,0,0,.12)}
.practice-photo{width:100%;height:100%}
.photo-contract{background:linear-gradient(135deg,#efece6 0%,#cfc7bb 45%,#8c8478 100%)}
.photo-migration{background:linear-gradient(135deg,#1e1e1e 0%,#4a4a4a 45%,#d9d9d9 60%,#3a3a3a 80%,#222 100%)}
.photo-boardroom{background:linear-gradient(180deg,#6e5a48 0%,#e6b27a 30%,#f4c38a 50%,#c48a54 70%,#2e2a28 100%)}
.practice-card{background:var(--white);text-align:center;padding:56px 24px 0}
.practice-card h3{font-family:"Libre Baskerville",serif;font-weight:400;font-size:15px;letter-spacing:1.5px;color:var(--ink);line-height:1.45;text-transform:uppercase}
.card-rule{width:72px;height:1px;background:var(--line);margin:22px auto}
.practice-card p{font-size:12.5px;line-height:1.7;color:var(--muted);padding:0 14px}
.practice-card .btn-dark{margin-top:20px;font-size:11px;padding:10px 16px}

/* about */
.about{position:absolute;top:1664px;left:0;width:1200px;height:555px;background:var(--panel)}
.about-photo{position:absolute;left:0;top:0;width:598px;height:555px;background:linear-gradient(120deg,#3a3f52 0%,#1d2230 45%,#4a5570 65%,#8a7d66 85%,#2a2520 100%)}
.about-copy{position:absolute;left:655px;top:60px;width:462px}
.about-copy h2{font-family:"Libre Baskerville",serif;font-weight:400;font-size:32px;color:var(--navy)}
.about-rule{width:72px;height:2px;background:var(--navy);margin:20px 0 22px}
.about-copy p{font-size:13.5px;line-height:1.75;color:var(--text);margin-bottom:18px}
.about-copy .btn-dark{margin-top:8px;padding:11px 28px}

/* blog */
.blog-cards{position:absolute;left:124px;top:2398px;display:flex;gap:30px}
.blog-card{width:297px;height:382px;background:var(--white);border:1px solid var(--line);box-shadow:0 1px 6px rgba(0,0,0,.08);padding:10px;text-align:center}
.blog-photo{height:178px;width:100%}
.bp-1{background:linear-gradient(135deg,#dfe2e6,#8d96a2 55%,#3e4652)}
.bp-2{background:linear-gradient(135deg,#f4f5f6,#c7ccd2 55%,#7e8790)}
.bp-3{background:linear-gradient(135deg,#8a5a34,#c08a5a 40%,#3a2616 75%,#1c130b)}
.blog-card h4{font-family:"Libre Baskerville",serif;font-weight:400;font-size:18px;color:var(--ink);margin:22px 0 8px;white-space:nowrap}
.blog-card p{font-size:12.5px;line-height:1.6;color:var(--text);padding:0 8px}
.btn-navy{display:inline-block;background:var(--navy);color:var(--white);font-size:12px;padding:10px 28px;margin-top:16px}

/* contact */
.contact{position:absolute;top:2900px;left:0;width:1200px;height:450px}
.map{position:absolute;left:0;top:0;width:600px;height:450px;background:linear-gradient(135deg,#e9e9e9,#d6d6d6 55%,#c9c9c9)}
.map-pin{position:absolute;left:312px;top:172px;width:34px;height:46px}
.contact-panel{position:absolute;left:600px;top:0;width:600px;height:450px;background:var(--navy);color:var(--white)}
.contact-pointer{position:absolute;left:-18px;top:90px;width:0;height:0;border-top:18px solid transparent;border-bottom:18px solid transparent;border-right:18px solid var(--navy)}
.contact-body{position:absolute;left:96px;top:92px}
.contact-kicker{font-size:21px}
.contact-body h2{font-family:"Libre Baskerville",serif;font-weight:400;font-size:30px;letter-spacing:1px;margin-top:8px}
.contact-rule{width:80px;height:1px;background:rgba(255,255,255,.5);margin:20px 0 26px}
.contact-line{display:flex;align-items:center;gap:10px;font-size:15px;margin-bottom:24px}
.contact-line svg{width:14px;height:14px;fill:var(--white)}
.social{display:flex;gap:14px}
.social span{width:11px;height:11px;border-radius:50%;background:var(--white)}

/* footer */
.site-footer{position:absolute;top:3350px;left:0;width:1200px;height:236px;background:var(--footer);color:var(--white)}
.footer-nav{position:absolute;left:88px;top:70px;display:flex;gap:22px;font-size:15px}
.footer-rule{position:absolute;left:88px;top:112px;width:662px;height:1px;background:#555}
.copyright{position:absolute;left:88px;top:138px;font-size:15px}
.footer-brand{position:absolute;left:900px;top:54px;width:230px;text-align:center}
.footer-brand .brand-square{width:62px;height:62px;background:var(--white);margin:0 auto 12px}
.footer-brand .brand-name{color:var(--white);font-size:24px;letter-spacing:4px}
</style>
</head>
<body>

<header class="site-header">
  <div class="brand"><div class="brand-square"></div><div class="brand-name">CORVELL<br>LEGAL</div></div>
  <div class="topbar">
    <svg viewBox="0 0 24 24"><path d="M6.6 10.8a15 15 0 006.6 6.6l2.2-2.2a1 1 0 011-.25 11.4 11.4 0 003.6.57 1 1 0 011 1V20a1 1 0 01-1 1A17 17 0 013 4a1 1 0 011-1h3.5a1 1 0 011 1 11.4 11.4 0 00.57 3.6 1 1 0 01-.25 1z"/></svg>
    <span>Call Us: +61 2 5550 1840</span><span class="sep">|</span>
    <svg viewBox="0 0 24 24"><path d="M2 5h20v14H2zm2 2v.5l8 6 8-6V7z"/></svg>
    <span>Mail To: info@corvelllegal.com</span>
  </div>
  <nav class="main-nav">
    <span>Home</span><span>About Us</span><span>What We Do</span><span>Blog</span><span>Contact Us</span>
    <span class="quote-btn">Get A Free Quote</span>
  </nav>
</header>

<section class="hero" role="img" aria-label="City harbour skyline at dusk with towers and water in the foreground">
  <div class="hero-box">
    <div class="hero-title">WE GET RESULTS.</div>
    <span class="btn-dark">READ MORE</span>
  </div>
</section>

<h2 class="section-title" style="top:736px">What We Do</h2>
<div class="section-rule" style="top:790px"></div>
<p class="section-sub" style="top:802px">We specialise in three main areas of Practice:</p>

<section class="practice-grid">
  <div class="practice-photo photo-contract" role="img" aria-label="Hands signing a contract on a desk beside a cup of coffee"></div>
  <div class="practice-card">
    <h3>Corporate Transactions<br>and Regulation</h3>
    <div class="card-rule"></div>
    <p>Sed ut perspiciatis unde omnis iste natus error sit voluptatem accusantium doloremque laudantium, totam rem aperiam, eaque ipsa quae ab illo inventore veritatis</p>
    <span class="btn-dark">CONTACT US NOW</span>
  </div>
  <div class="practice-photo photo-migration" role="img" aria-label="Person in a dark suit holding an immigration law sign"></div>
  <div class="practice-card">
    <h3>Business Law and<br>Dispute Resolution</h3>
    <div class="card-rule"></div>
    <p>Sed ut perspiciatis unde omnis iste natus error sit voluptatem accusantium doloremque laudantium, totam rem aperiam, eaque ipsa quae ab illo inventore veritatis</p>
    <span class="btn-dark">CONTACT US NOW</span>
  </div>
  <div class="practice-photo photo-boardroom" role="img" aria-label="Silhouetted business meeting in a sunlit boardroom"></div>
  <div class="practice-card">
    <h3>Migration<br>Assistance</h3>
    <div class="card-rule"></div>
    <p>Sed ut perspiciatis unde omnis iste natus error sit voluptatem accusantium doloremque laudantium, totam rem aperiam, eaque ipsa quae ab illo inventore veritatis</p>
    <span class="btn-dark">CONTACT US NOW</span>
  </div>
</section>

<section class="about">
  <div class="about-photo" role="img" aria-label="Portrait of the principal lawyer in a suit against a night city skyline"></div>
  <div class="about-copy">
    <h2>About Marcus Corvell</h2>
    <div class="about-rule"></div>
    <p>Marcus's rare regulatory experience in public fundraisings and mergers and acquisitions is a compelling advantage for any company seeking to complete a significant transaction quickly.</p>
    <p>Marcus assisted draft the Commission's regulatory guidance on prospectuses. With his team Marcus was awarded an Australia Day Achievement Medallion, "reserved for the highest level of recognition", and awarded "to recognise the significant contribution made to the nation by individuals in the public service".</p>
    <p>Marcus guides corporate transactions through the regulatory hurdles to help minimise the chance of failure and delay, and maximise your chance of success.</p>
    <span class="btn-dark">READ MORE</span>
  </div>
</section>

<h2 class="section-title" style="top:2302px">From Our Blog</h2>
<div class="section-rule" style="top:2356px"></div>

<section class="blog-cards">
  <article class="blog-card">
    <div class="blog-photo bp-1" role="img" aria-label="Two businessmen shaking hands in an office"></div>
    <h4>The standard Lorem Ipsum</h4>
    <p>On the other hand, we denounce with righteous indignation and dislike men who are so beguiled and demoralized by the charms of pleasure of the moment,</p>
    <span class="btn-navy">Read More</span>
  </article>
  <article class="blog-card">
    <div class="blog-photo bp-2" role="img" aria-label="Documents being stamped on a desk"></div>
    <h4>Finibus Bonorum Malorum</h4>
    <p>On the other hand, we denounce with righteous indignation and dislike men who are so beguiled and demoralized by the charms of pleasure of the moment,</p>
    <span class="btn-navy">Read More</span>
  </article>
  <article class="blog-card">
    <div class="blog-photo bp-3" role="img" aria-label="Close-up of a handshake"></div>
    <h4>At vero eos et accusamus</h4>
    <p>On the other hand, we denounce with righteous indignation and dislike men who are so beguiled and demoralized by the charms of pleasure of the moment,</p>
    <span class="btn-navy">Read More</span>
  </article>
</section>

<section class="contact">
  <div class="map" role="img" aria-label="Street map showing the office location">
    <svg class="map-pin" viewBox="0 0 24 32" aria-hidden="true"><path d="M12 0A12 12 0 000 12c0 9 12 20 12 20s12-11 12-20A12 12 0 0012 0zm0 17a5 5 0 110-10 5 5 0 010 10z" fill="#e0504a"/></svg>
  </div>
  <div class="contact-panel">
    <div class="contact-pointer"></div>
    <div class="contact-body">
      <div class="contact-kicker">Contact Us</div>
      <h2>Get In Touch</h2>
      <div class="contact-rule"></div>
      <div class="contact-line"><svg viewBox="0 0 24 24"><path d="M12 2a7 7 0 00-7 7c0 5 7 13 7 13s7-8 7-13a7 7 0 00-7-7zm0 9.5A2.5 2.5 0 1112 6.5a2.5 2.5 0 010 5z"/></svg>42 Harbour Lane, Westmere, Sydney, 2019.</div>
      <div class="contact-line"><svg viewBox="0 0 24 24"><path d="M6.6 10.8a15 15 0 006.6 6.6l2.2-2.2a1 1 0 011-.25 11.4 11.4 0 003.6.57 1 1 0 011 1V20a1 1 0 01-1 1A17 17 0 013 4a1 1 0 011-1h3.5a1 1 0 011 1 11.4 11.4 0 00.57 3.6 1 1 0 01-.25 1z"/></svg>Call: +61 2 5550 1840</div>
      <div class="contact-line"><svg viewBox="0 0 24 24"><path d="M2 5h20v14H2zm2 2v.5l8 6 8-6V7z"/></svg>Mail: info@corvelllegal.com</div>
      <div class="social"><span></span><span></span><span></span><span></span></div>
    </div>
  </div>
</section>

<footer class="site-footer">
  <nav class="footer-nav"><span>Home</span><span>|</span><span>About Us</span><span>|</span><span>What We Do</span><span>|</span><span>Blog</span><span>|</span><span>Contact Us</span></nav>
  <div class="footer-rule"></div>
  <div class="copyright">Corvell Legal &nbsp;© 2018 All Rights Reserved</div>
  <div class="footer-brand"><div class="brand-square"></div><div class="brand-name">CORVELL<br>LEGAL</div></div>
</footer>

</body>
</html>
```